revised: 'kelvale ironworks' logo -or- business card

we require a business card or a logo that can be used on a business card & other stationery

(i've just recently decided to open this contest up to logo designs as well - but if you have already been working on a card concept, please feel free to continue with it & submit!)

-

We design and build custom brackets and fixings for our customers and their castles, i.e. homes, offices, workshops, farms etc. Our products might be used to:
- brace or support structures, such as houses, decks, small bridges, etc.
- connect any building material to another
- or could simply be a unique piece that exists as a talking point

As part of our design process we would produce drawings/plans/blue prints/prototypes of the product. Our designs factor in multiple elements, from the materials being joined, the client's taste, and the overall durability demanded by the application - if necessary, the bracket may also be endorsed by a third party, such as a stuctural or mechanical engineer.

The build process takes part in our workshop and on the client's site - some elements may be manufactured off-site, depending on the design chosen and the materials used.

Our brackets are designed to our customers' tastes and could be made to be hidden within the structure or exposed to create interest. Our brackets can be large or small, or be neat with clean lines or take on more of an industrial look.
Updates

please note brief has been updated with a more specific description of our business activity

i have also added the final drawing that was used to water-jet the bracket shown in the photos

also, you will note i changed the title to 'logo + business card'

i don't expect a logo as a discrete artefact of the job, however, i expect that some or all elements on the face of the business card will lend themselves to the street sign (as stated in the original brief) as well as any future logo used on letter heads, invoices, etcetera

another update - changed the allowable entries to include logo's only, as well as business cards

Industry/Entity Type

Industrial

Requirements
Must have
• the face should have the name 'Kelvale Ironworks' (or no/all-caps)

the number '75' in the logo, which will also be turned into a conservative (residential) street sign ('75' being a street number) - '75' should stand alone -OR- be readily identified by someone who has previously received a business card

i need to make this '75' and any associated 'framing', so it should be transferrable to cad/dxf for machining, laser/water-cutting, brazing/welding, etcet.

(on that note, the winning designer will be able to share their vision for this sign and we'll adhere to it ... within the realms of possibility! if you're happy with the result then you could include it in your portfolio)
Nice to have
• one side of the card needs a majority of space for quotes, hand-written information, etcet. so this side should be white or a light, complimentary colour suitable for black/blue pen

the following should appear somewhere on the card (there is no email or website) :
- name : Dana Morrow (Proprietor)
- mobile phone number : +61 (0) 498 761203
- abn: 58 904 617 235

any combination of the following (or equivalent) text:

* 'your castle' - this is slang for your house/place (i prefer this to 'home' as 1: it can apply to a place of business, and 2: for me at least, it conjurs images of wrought iron, brass, hardwood & stone)

* unique

* ...

```html
<!DOCTYPE html>
<html lang="en">
<head>
<meta charset="utf-8">
<title>Kelvale Ironworks — Business Card</title>
<link rel="stylesheet" href="https://fonts.googleapis.com/css2?family=Arimo:wght@400&display=swap">
<style>
  :root {
    --page: #ffffff;
    --card: #ffffff;
    --card-edge: #9a9a9a;
    --ink: #1a1a1a;
    --muted: #b4b4b4;
    --faint: #ececec;
    --band: #000000;
  }
  * { margin: 0; padding: 0; box-sizing: border-box; }
  html, body {
    width: 845px;
    height: 1200px;
    overflow: hidden;
    background: var(--page);
    font-family: "Arimo", Arial, sans-serif;
    color: var(--ink);
  }
  .sheet { position: relative; width: 845px; height: 1200px; }
  .card {
    position: absolute;
    left: 184px;
    width: 495px;
    height: 322px;
    background: var(--card);
    border: 1px solid var(--card-edge);
    overflow: hidden;
  }
  .card--front { top: 256px; }
  .card--back { top: 661px; }
  .card__ring {
    position: absolute;
    left: 225px;
    top: 30px;
    width: 246px;
    height: 246px;
  }
  .card__band {
    position: absolute;
    left: 0; right: 0; bottom: 0;
    height: 23px;
    background: var(--band);
  }
  .brand {
    position: absolute;
    left: 35px;
    top: 36px;
    display: flex;
    align-items: center;
  }
  .brand__circle {
    width: 72px;
    height: 72px;
    border: 2.5px solid var(--ink);
    border-radius: 50%;
    flex: none;
  }
  .brand__text { margin-left: 18px; margin-top: 8px; }
  .brand__name {
    font-size: 24px;
    line-height: 1;
    letter-spacing: 0.2px;
    color: var(--ink);
  }
  .brand__tagline {
    margin-top: 6px;
    font-size: 14.5px;
    color: var(--muted);
  }
  .contact {
    position: absolute;
    left: 125px;
    top: 196px;
    font-size: 15px;
    line-height: 19px;
  }
  .contact__name { font-size: 17px; margin-bottom: 13px; }
  .contact__role { font-size: 13px; }
</style>
</head>
<body>
<main class="sheet">
  <section class="card card--front" aria-label="Card front">
    <svg class="card__ring" viewBox="0 0 246 246" aria-hidden="true">
      <circle cx="123" cy="123" r="119" fill="none" stroke="var(--faint)" stroke-width="7"/>
    </svg>
    <div class="brand">
      <div class="brand__circle" aria-hidden="true"></div>
      <div class="brand__text">
        <div class="brand__name">Kelvale Ironworks</div>
        <div class="brand__tagline">Bespoke Bracket Manufacturing Service</div>
      </div>
    </div>
    <div class="contact">
      <p class="contact__name">Dana Morrow <span class="contact__role">(Proprietor)</span></p>
      <p>Mobile : +61 (0) 498 761203</p>
      <p>Abn: 58 904 617 235</p>
    </div>
    <div class="card__band"></div>
  </section>

  <section class="card card--back" aria-label="Card back">
    <svg class="card__ring" viewBox="0 0 246 246" aria-hidden="true">
      <circle cx="123" cy="123" r="119" fill="none" stroke="var(--faint)" stroke-width="7"/>
    </svg>
    <div class="card__band"></div>
  </section>
</main>
</body>
</html>
```